Business Card Design Project

We need a Business Card for an Mechanical Engineering firm in Singapore. The design should be Modern & Technical looking, yet eye catching.

Our company deals in Cutting Tools & Machine Accessories for the Manufacturing Industries such as Oil & Gas, Aero Space, etc... For more information on our Company, you can either email me or view our website www.torvalen.com.sg.

We are trying to revamp our image to give our consumers a fresh new perspective to our company, so we welcome all ideas.

Industry/Entity Type

Business

Requirements
Must have
• Must incorporate New Company Logo into the card as shown in Uploaded file.

```html
<!DOCTYPE html>
<html lang="en">
<head>
<meta charset="utf-8">
<title>Torvalen Tools – Business Card</title>
<link rel="stylesheet" href="https://fonts.googleapis.com/css2?family=Arimo:wght@400;700&display=swap">
<style>
  :root {
    --bg-light: #f4f4f4;
    --bg-dark: #9a9a9a;
    --card-black: #1e1b1b;
    --card-white: #ffffff;
    --brand-red: #8c2326;
    --brand-red-light: #a8353a;
    --ink-dark: #2a2626;
    --ink-light: #ffffff;
    --ink-muted: #f1dcdc;
  }
  html, body {
    margin: 0;
    padding: 0;
    width: 1200px;
    height: 951px;
    overflow: hidden;
  }
  body {
    position: relative;
    background: radial-gradient(ellipse at 50% 45%, var(--bg-light) 0%, #d6d6d6 60%, var(--bg-dark) 100%);
    font-family: "Arimo", Arial, sans-serif;
  }
  .card {
    position: absolute;
    border-radius: 22px;
    overflow: hidden;
    box-shadow: 0 10px 28px rgba(0,0,0,0.28);
  }

  /* Front card */
  .card-front {
    left: 60px;
    top: 100px;
    width: 620px;
    height: 354px;
    background: var(--card-black);
    color: var(--ink-light);
  }
  .card-front .brand {
    position: absolute;
    left: 0;
    right: 0;
    top: 128px;
    display: flex;
    justify-content: center;
    align-items: center;
    gap: 16px;
  }
  .brand-dot {
    width: 30px;
    height: 30px;
    border-radius: 50%;
    background: var(--brand-red-light);
    flex: none;
  }
  .brand-name {
    font-family: "Arimo", Arial, sans-serif;
    font-weight: 700;
    letter-spacing: 1px;
    text-transform: uppercase;
  }
  .card-front .brand-name {
    font-size: 52px;
    color: var(--ink-light);
  }
  .card-front .website {
    position: absolute;
    left: 0;
    right: 0;
    top: 262px;
    text-align: center;
    font-size: 20px;
    letter-spacing: 0.5px;
  }

  /* Back card */
  .card-back {
    left: 350px;
    top: 456px;
    width: 800px;
    height: 457px;
    background: var(--card-white);
    color: var(--ink-dark);
  }
  .card-back .swoosh {
    position: absolute;
    inset: 0;
    width: 100%;
    height: 100%;
  }
  .card-back .brand {
    position: absolute;
    left: 96px;
    top: 62px;
    display: flex;
    align-items: center;
    gap: 12px;
  }
  .card-back .brand-dot {
    width: 24px;
    height: 24px;
    background: var(--brand-red);
  }
  .card-back .brand-name {
    font-size: 40px;
    color: var(--brand-red);
  }
  .address {
    position: absolute;
    left: 96px;
    top: 160px;
    display: flex;
    gap: 12px;
    font-size: 22px;
    line-height: 28px;
  }
  .contacts {
    position: absolute;
    left: 96px;
    top: 262px;
    margin: 0;
    padding: 0;
    list-style: none;
    font-size: 22px;
    line-height: 30px;
  }
  .contacts li {
    display: flex;
    align-items: center;
    gap: 12px;
  }
  .icon {
    width: 20px;
    height: 20px;
    flex: none;
    fill: var(--brand-red);
  }
  .address .icon { margin-top: 3px; }
  .web-link { color: var(--brand-red); }
  .person {
    position: absolute;
    right: 70px;
    top: 336px;
    text-align: center;
    color: var(--ink-light);
  }
  .person-name {
    font-size: 30px;
    letter-spacing: 0.5px;
  }
  .person-role {
    font-size: 20px;
    color: var(--ink-muted);
    margin-top: 4px;
  }
</style>
</head>
<body>

  <section class="card card-front">
    <div class="brand">
      <span class="brand-dot"></span>
      <span class="brand-name">Torvalen Tools</span>
    </div>
    <div class="website">www.torvalentools.com</div>
  </section>

  <section class="card card-back">
    <svg class="swoosh" viewBox="0 0 800 457" preserveAspectRatio="none" aria-hidden="true">
      <path d="M470 0 C600 60 530 200 470 300 C430 370 420 420 430 457 L800 457 L800 0 Z" fill="var(--card-black)"/>
      <path d="M540 0 C640 70 590 200 540 290 C500 360 490 420 500 457 L800 457 L800 0 Z" fill="var(--brand-red)"/>
    </svg>

    <div class="brand">
      <span class="brand-dot"></span>
      <span class="brand-name">Torvalen Tools</span>
    </div>

    <div class="address">
      <svg class="icon" viewBox="0 0 20 20" aria-hidden="true"><path d="M10 2 L19 10 L16 10 L16 18 L12 18 L12 13 L8 13 L8 18 L4 18 L4 10 L1 10 Z"/></svg>
      <div>1480 Marlow Crest Rd.<br>Brenfield, TX 78940</div>
    </div>

    <ul class="contacts">
      <li>
        <svg class="icon" viewBox="0 0 20 20" aria-hidden="true"><path d="M5 2 L8 2 L9 6 L7 8 C8 11 9 12 12 13 L14 11 L18 12 L18 15 C18 17 16 18 14 18 C7 17 3 13 2 6 C2 4 3 2 5 2 Z"/></svg>
        <span>555-014-2290</span>
      </li>
      <li>
        <svg class="icon" viewBox="0 0 20 20" aria-hidden="true"><path d="M6 1 H14 A1.5 1.5 0 0 1 15.5 2.5 V17.5 A1.5 1.5 0 0 1 14 19 H6 A1.5 1.5 0 0 1 4.5 17.5 V2.5 A1.5 1.5 0 0 1 6 1 Z M6.5 4 V14 H13.5 V4 Z"/></svg>
        <span>555-014-2291</span>
      </li>
      <li>
        <svg class="icon" viewBox="0 0 20 20" aria-hidden="true"><path d="M2 5 H18 V16 H2 Z M3 6 L10 11 L17 6 Z" fill-rule="evenodd"/></svg>
        <span>info@torvalentools.com</span>
      </li>
      <li>
        <svg class="icon" viewBox="0 0 20 20" aria-hidden="true"><circle cx="10" cy="10" r="8"/></svg>
        <span class="web-link">www.torvalentools.com</span>
      </li>
    </ul>

    <div class="person">
      <div class="person-name">Marcus Ellery</div>
      <div class="person-role">director</div>
    </div>
  </section>

</body>
</html>
```